Professional Single Page Website Design for Tollbrook Advisory

Tollbrook Advisory is a new business consultancy specializing in providing expert services to small businesses, primarily in the brick-and-mortar retail and food service sectors. We offer a range of services including franchise development and launch, due diligence, and construction management.

Currently, we have a basic website set up at www.tollbrookadvisory.example, but we need a professional touch to enhance its design and functionality.

Project Requirements:
- Single Page Design: For now, we need a single page design that effectively showcases who we are, our services, and contact information.
- Future Expansion: The design should be flexible and scalable for future expansion to include additional pages like specific service offerings, about us, and a dedicated contact page.
- Design Aesthetic: We are looking for a modern yet professional design that aligns with our brand identity.
- Logo: We have a logo that we like, which was also sourced from Pixel Bazaar. The logo files are attached to this project brief.

Key Sections to Include:
- Hero Section: An engaging introduction to Tollbrook Advisory with a strong visual impact.
- About Us: A brief overview of who we are and our mission.
- Team: Section for the profiles of the two principals.
- Services: A clear and concise presentation of our services, including franchise development, due diligence, and construction management.
- Contact Information: Easy-to-find contact details, including a form for inquiries.
- Call to Action: Encouraging visitors to get in touch with us for consultations or further information.

Design Considerations:
- Ensure the design is responsive and mobile-friendly.
- Include high-quality images and icons that complement our services and industry.
- We do not need development services, this is only a design project.

```html
<!DOCTYPE html>
<html lang="en">
<head>
<meta charset="utf-8">
<title>Tollbrook Advisory</title>
<link rel="stylesheet" href="https://fonts.googleapis.com/css2?family=Poppins:wght@400;500;600;700&display=swap">
<style>
:root{
  --teal:#8ec4aa;
  --teal-soft:#9dcbb6;
  --teal-text:#7fbf9f;
  --ink:#1d2a33;
  --navy:#243645;
  --navy-deep:#1f2e3a;
  --white:#ffffff;
  --muted:#3b4a55;
}
*{box-sizing:border-box;margin:0;padding:0}
html,body{width:1200px;height:4021px;overflow:hidden}
body{position:relative;font-family:'Poppins',sans-serif;color:var(--ink);background:var(--white)}
.abs{position:absolute}
.fill{position:absolute}
.logo{display:flex;align-items:center;gap:12px}
.logo-mark{width:56px;height:56px;border-radius:50%;background:var(--teal)}
.logo-name{font-weight:600;font-size:20px;line-height:1.1;color:var(--ink);width:130px}
.nav{top:0;left:0;width:1200px;height:100px}
.nav a{position:absolute;top:38px;font-size:15px;color:var(--ink);text-decoration:none}
.nav a.active{border-bottom:2px solid var(--teal);padding-bottom:4px}
.nav .sep{position:absolute;top:42px;width:1px;height:13px;background:#556}
.pill{display:flex;align-items:center;justify-content:center;border-radius:22px;background:var(--teal);color:var(--ink);font-size:14px;font-weight:500}
.eyebrow{font-size:13px;letter-spacing:1.5px;text-align:center}
.h2{font-size:40px;font-weight:700;text-align:center}
.accent{color:var(--teal-text)}
.card{background:var(--white)}
.card .name{font-size:20px;font-weight:700}
.card .role{font-size:17px;color:var(--muted)}
.card .bio{font-size:10.5px;line-height:17.5px;margin-top:12px;width:230px}
.dots{display:flex;gap:22px;margin-top:12px}
.dots i{width:12px;height:12px;border-radius:50%;border:2px solid var(--teal)}
.svc{border:2px solid var(--teal-soft);text-align:center;padding:66px 28px 0}
.svc h3{font-size:18px;font-weight:600;line-height:21px;margin-bottom:18px}
.svc p{font-size:11px;line-height:19.5px;color:var(--muted)}
.svc.dark{background:var(--navy);border-color:var(--navy)}
.svc.dark h3,.svc.dark p{color:var(--white)}
.icon-dia{width:74px;height:74px;background:var(--teal);border-radius:14px;transform:rotate(45deg)}
.field{background:var(--white);font-size:12px;color:#555;padding:14px 20px}
.contact-item{display:flex;align-items:center;gap:22px;color:var(--white)}
.contact-item .lbl{font-size:17px}
.contact-item .val{font-size:17px;color:var(--teal-text)}
.foot h4{font-size:18px;font-weight:600;margin-bottom:18px}
.foot li{list-style:none;font-size:13px;line-height:23px}
.foot .row{display:flex;align-items:center;gap:10px;font-size:13px;margin-bottom:22px}
.foot .dot{width:26px;height:26px;border-radius:50%;background:var(--teal-soft)}
.vline{width:2px;background:#4a5a66}
.vdot{width:10px;height:10px;border-radius:50%;background:#4a5a66}
</style>
</head>
<body>

<!-- HERO -->
<div class="fill" style="top:0;left:0;width:1200px;height:715px;background:linear-gradient(180deg,#cfe3ec 0%,#e7ecee 35%,#d8cdbd 60%,#9a968f 100%)" role="img" aria-label="Modern commercial retail building with orange awnings and stone facade under a blue sky"></div>
<svg class="abs" style="top:600px;left:0" width="1200" height="120" viewBox="0 0 1200 120">
  <polygon points="0,120 0,100 600,10 1200,110 1200,120" fill="#fff"/>
  <polygon points="0,100 600,10 600,18 0,112" fill="var(--teal)"/>
  <polygon points="600,10 1200,100 1200,110 600,18" fill="#1a1a1a"/>
</svg>

<nav class="nav abs">
  <div class="logo abs" style="left:118px;top:20px"><div class="logo-mark"></div><div class="logo-name">Tollbrook Advisory</div></div>
  <a class="active" style="left:401px">Home</a><span class="sep" style="left:475px"></span>
  <a style="left:508px">About</a><span class="sep" style="left:585px"></span>
  <a style="left:616px">Services</a><span class="sep" style="left:708px"></span>
  <a style="left:741px">Team</a><span class="sep" style="left:815px"></span>
  <a style="left:847px">Contact</a>
  <div class="pill abs" style="left:950px;top:29px;width:146px;height:41px">Get in touch</div>
</nav>

<div class="abs" style="left:118px;top:190px">
  <h1 style="font-size:41px;font-weight:700;line-height:46px">Building Success in<br><span class="accent" style="font-size:47px">Southern California</span></h1>
  <p style="font-size:20px;font-weight:500;line-height:31px;margin-top:10px">Expertise at Every Step:<br>From Planning to Execution</p>
  <div class="pill" style="width:145px;height:38px;margin-top:22px;font-size:13px">Learn More ›</div>
</div>
<div class="abs vline" style="left:598px;top:612px;height:60px"></div>
<div class="abs vdot" style="left:594px;top:671px"></div>

<!-- WHO WE ARE -->
<p class="abs eyebrow" style="left:0;width:1210px;top:727px">TOLLBROOK ADVISORY</p>
<h2 class="abs h2" style="left:0;width:1210px;top:745px">Who We <span class="accent">Are</span></h2>
<svg class="abs" style="left:95px;top:765px" width="510" height="520" viewBox="0 0 510 520" role="img" aria-label="Photos of modern storefront buildings inside rounded diamond frames">
  <defs><linearGradient id="bld" x1="0" y1="0" x2="0" y2="1"><stop offset="0" stop-color="#4a86c6"/><stop offset=".5" stop-color="#c9b15a"/><stop offset="1" stop-color="#6f6c6a"/></linearGradient></defs>
  <rect x="85" y="55" width="300" height="300" rx="70" transform="rotate(45 235 205)" fill="none" stroke="var(--teal)" stroke-width="12"/>
  <rect x="100" y="70" width="270" height="270" rx="60" transform="rotate(45 235 205)" fill="url(#bld)"/>
  <rect x="290" y="305" width="160" height="160" rx="36" transform="rotate(45 370 385)" fill="#8d6b5a" stroke="#fff" stroke-width="8"/>
</svg>
<div class="abs" style="left:617px;top:836px;width:510px">
  <p style="font-size:17px;font-weight:500;line-height:27px">Welcome to Tollbrook Advisory, your trusted partner in navigating the complexities of the real estate and small business markets.</p>
  <p style="font-size:16px;line-height:24.7px;margin-top:22px;color:var(--muted)">Founded by industry veterans Marco Delvane and Milo Tanaka, we specialize in providing comprehensive services tailored to the unique needs of our clients. Whether you're a franchisee, a new restaurant owner, or a commercial real estate investor, our expertise in due diligence, construction management, and investment property evaluation ensures you make informed, strategic decisions. Discover how Tollbrook Advisory can support your business journey. Partner with us and experience the difference our dedication and expertise can make.</p>
</div>

<!-- TEAM BAND + MISSION -->
<div class="fill" style="left:0;top:1557px;width:1200px;height:618px;background:var(--teal)"></div>
<div class="fill" style="left:89px;top:1318px;width:1019px;height:330px;border-radius:12px;background:linear-gradient(90deg,#2a4152,#34495a 60%,#27394a)" role="img" aria-label="Dusk view of a commercial building with a dark overlay"></div>
<p class="abs" style="left:161px;top:1430px;font-size:13px;letter-spacing:1.5px;color:#fff">TOLLBROOK ADVISORY</p>
<h2 class="abs" style="left:160px;top:1450px;font-size:41px;font-weight:700;color:#fff">Our Mission</h2>
<p class="abs" style="left:508px;top:1408px;width:510px;font-size:16.5px;line-height:24.7px;color:#fff">At Tollbrook Advisory, we are committed to your success. Our approach combines meticulous analysis, strategic insights, and personalized service to help you achieve your business goals. We pride ourselves on our ability to deliver results that exceed expectations, fostering long-term relationships built on trust and excellence.</p>

<p class="abs eyebrow" style="left:0;width:1224px;top:1701px;color:#fff">LEADERSHIP TEAM</p>
<h2 class="abs h2" style="left:0;width:1224px;top:1718px;color:#fff">Meet the Team</h2>

<div class="abs card" style="left:103px;top:1828px;width:479px;height:249px"></div>
<div class="fill" style="left:111px;top:1850px;width:178px;height:200px;background:linear-gradient(180deg,#9fc3df,#e9ecef)" role="img" aria-label="Portrait photo of Marco Delvane"></div>
<div class="abs" style="left:310px;top:1865px">
  <p class="name card" style="background:none">Marco Delvane</p>
  <div class="card" style="background:none"><p class="role">Principal</p>
  <p class="bio">Marco Delvane brings almost 20 years of rich experience as a real estate investor and a pivotal role at one of the region's largest real estate management firms, where he…</p></div>
  <div class="dots"><i></i><i></i><i></i></div>
</div>

<div class="abs card" style="left:620px;top:1828px;width:473px;height:249px"></div>
<div class="fill" style="left:624px;top:1852px;width:176px;height:200px;background:linear-gradient(180deg,#8b8e8c,#3b3d40)" role="img" aria-label="Portrait photo of Milo Tanaka"></div>
<div class="abs" style="left:824px;top:1865px">
  <p class="name" style="font-size:20px;font-weight:700">Milo Tanaka</p>
  <p class="role" style="font-size:17px;color:var(--muted)">Principal</p>
  <p style="font-size:10.5px;line-height:17.5px;margin-top:12px;width:230px">Milo Tanaka is a seasoned real estate expert with extensive experience in project and construction management, and a licensed real estate agent in the state. Fluent in two languages.</p>
  <div class="dots"><i></i><i></i><i></i></div>
</div>

<div class="abs vline" style="left:621px;top:2150px;height:62px"></div>
<div class="abs vdot" style="left:617px;top:2211px"></div>

<!-- SERVICES -->
<p class="abs eyebrow" style="left:0;width:1244px;top:2264px">WHAT WE DO</p>
<h2 class="abs h2" style="left:0;width:1244px;top:2282px">Tollbrook <span class="accent">Services</span></h2>

<div class="abs svc" style="left:141px;top:2423px;width:304px;height:344px">
  <h3>Franchise development and launch</h3>
  <p>At Tollbrook Advisory, our Franchise Development &amp; Launch service is designed to transform your successful business into a thriving franchise. We start by thoroughly evaluating your business model to determine its franchisability.</p>
</div>
<div class="abs svc dark" style="left:468px;top:2423px;width:304px;height:344px">
  <h3>Due Diligence</h3>
  <p>Tollbrook offers comprehensive evaluations tailored to your business needs. We meticulously assess franchise opportunities, business sales, and property transactions, identifying potential risks and liabilities to safeguard your investments. Our expert team provides actionable recommendations on deal points and offers strategic guidance throughout the entire process.</p>
</div>
<div class="abs svc" style="left:795px;top:2423px;width:304px;height:344px">
  <h3>Construction Management</h3>
  <p>Our Building &amp; Construction Management Services oversee every aspect of your construction and development projects, from initial planning to final completion. We ensure projects stay on time and within budget, providing meticulous attention to detail and proactive problem-solving.</p>
</div>
<div class="abs icon-dia" style="left:256px;top:2382px"></div>
<div class="abs icon-dia" style="left:583px;top:2382px"></div>
<div class="abs icon-dia" style="left:910px;top:2382px"></div>
<svg class="abs" style="left:268px;top:2394px" width="50" height="50" viewBox="0 0 50 50" fill="none" stroke="#fff" stroke-width="2"><rect x="17" y="17" width="16" height="14"/><circle cx="25" cy="10" r="3"/><circle cx="10" cy="25" r="3"/><circle cx="40" cy="25" r="3"/><circle cx="25" cy="40" r="3"/></svg>
<svg class="abs" style="left:595px;top:2394px" width="50" height="50" viewBox="0 0 50 50" fill="none" stroke="#fff" stroke-width="2"><rect x="12" y="8" width="20" height="28"/><circle cx="30" cy="32" r="7"/><line x1="35" y1="37" x2="42" y2="44"/></svg>
<svg class="abs" style="left:922px;top:2394px" width="50" height="50" viewBox="0 0 50 50" fill="none" stroke="#fff" stroke-width="2"><rect x="8" y="22" width="26" height="20"/><circle cx="36" cy="14" r="7"/><line x1="14" y1="30" x2="28" y2="30"/></svg>

<!-- CONTACT -->
<div class="fill" style="left:0;top:2850px;width:1200px;height:895px;background:linear-gradient(180deg,#26384a,#1f2e3a)" role="img" aria-label="Darkened photo of a commercial building at night"></div>
<svg class="abs" style="left:0;top:2840px" width="1200" height="120" viewBox="0 0 1200 120">
  <polygon points="0,0 1200,0 1200,12 600,12 0,110" fill="#fff"/>
  <polygon points="0,100 600,12 600,22 0,112" fill="var(--teal)"/>
  <polygon points="600,12 1200,12 1200,80" fill="var(--navy-deep)"/>
</svg>
<p class="abs eyebrow" style="left:0;width:1196px;top:2954px;color:var(--teal-text)">GET IN TOUCH</p>
<h2 class="abs h2" style="left:0;width:1196px;top:2972px;color:#fff">Contact Tollbrook</h2>
<div class="abs" style="left:567px;top:3033px;width:60px;height:3px;background:var(--teal)"></div>

<div class="abs contact-item" style="left:140px;top:3102px">
  <svg width="80" height="80" viewBox="0 0 80 80" fill="none" stroke="#fff" stroke-width="1.5"><rect x="16" y="16" width="48" height="48" rx="6" transform="rotate(45 40 40)"/><path d="M40 52c-6-8-9-12-9-17a9 9 0 0 1 18 0c0 5-3 9-9 17z"/><circle cx="40" cy="35" r="3"/></svg>
  <div><p class="lbl">Address</p><p class="val">412 Harbor Crest Ave,<br>Lakeview, CA 90000</p></div>
</div>
<div class="abs contact-item" style="left:443px;top:3102px">
  <svg width="80" height="80" viewBox="0 0 80 80" fill="none" stroke="#fff" stroke-width="1.5"><rect x="16" y="16" width="48" height="48" rx="6" transform="rotate(45 40 40)"/><rect x="28" y="32" width="24" height="16"/><path d="M28 32l12 9 12-9"/></svg>
  <div><p class="lbl">Email Us</p><p class="val">enquiry@tollbrookadvisory.example</p></div>
</div>
<div class="abs contact-item" style="left:845px;top:3102px">
  <svg width="80" height="80" viewBox="0 0 80 80" fill="none" stroke="#fff" stroke-width="1.5"><rect x="16" y="16" width="48" height="48" rx="6" transform="rotate(45 40 40)"/><path d="M32 30l5-2 3 6-3 2c2 4 4 6 8 8l2-3 6 3-2 5c-10 0-19-9-19-19z"/></svg>
  <div><p class="lbl">Phone number</p><p class="val">(555) 014 2290</p></div>
</div>

<div class="abs" style="left:206px;top:3255px;width:803px;height:440px;background:var(--teal-soft)"></div>
<p class="abs" style="left:206px;width:803px;top:3296px;text-align:center;font-size:30px;font-weight:600;color:#fff">Leave us a Message</p>
<div class="abs field" style="left:271px;top:3353px;width:327px;height:42px">First Name</div>
<div class="abs field" style="left:610px;top:3353px;width:328px;height:42px">Last Name</div>
<div class="abs field" style="left:271px;top:3410px;width:327px;height:42px">Email address</div>
<div class="abs field" style="left:610px;top:3410px;width:328px;height:42px">Phone</div>
<div class="abs field" style="left:273px;top:3468px;width:667px;height:95px">Leave message</div>
<div class="abs pill" style="left:525px;top:3580px;width:173px;height:45px;background:var(--navy);color:#fff;font-size:13px;font-weight:600">SEND MESSAGE</div>

<!-- FOOTER -->
<footer class="abs foot" style="left:0;top:3745px;width:1200px;height:276px">
  <div class="logo abs" style="left:124px;top:52px"><div class="logo-mark" style="width:62px;height:62px"></div><div class="logo-name">Tollbrook Advisory</div></div>
  <p class="abs" style="left:133px;top:140px;font-size:13px;line-height:19px">© 2024 Tollbrook Advisory<br>All Right Reserved</p>
  <div class="abs" style="left:383px;top:0;width:1px;height:276px;background:#dde3e0"></div>
  <div class="abs" style="left:593px;top:0;width:1px;height:276px;background:#dde3e0"></div>
  <div class="abs" style="left:925px;top:0;width:1px;height:276px;background:#dde3e0"></div>
  <div class="abs" style="left:413px;top:62px">
    <h4>Navigation</h4>
    <ul><li style="text-decoration:underline">Home</li><li>About Us</li><li>Team</li><li>Services</li><li>Contact Us</li></ul>
  </div>
  <div class="abs" style="left:617px;top:62px">
    <h4>Contact Us</h4>
    <div class="row"><span class="dot"></span>412 Harbor Crest Ave, Lakeview, CA 90000</div>
    <div class="row"><span class="dot"></span>(555) 014 2290</div>
    <div class="row"><span class="dot"></span>enquiry@tollbrookadvisory.example</div>
  </div>
  <div class="abs" style="left:951px;top:62px">
    <h4>Follow us</h4>
    <div style="display:flex;gap:22px"><span class="dot" style="width:26px;height:26px;border-radius:50%;background:var(--navy)"></span><span style="width:26px;height:26px;border-radius:50%;background:var(--navy)"></span><span style="width:26px;height:26px;border-radius:50%;background:var(--navy)"></span></div>
  </div>
</footer>

</body>
</html>
```